Graphic Design Project

Hi Designers
New Label for New Rum .
The label we would like is it to be modern and smart looking, simple and eye catching. Ingenuity is required and a great open mind to creating this label. Type of rum -Rich flavour with a smooth rounded character. It has robust fruity flavours of molasses, honey and chocolate and is not as sweet as other rums, giving it a strong dark rum taste for the "real rum drinker. If you google Crimson Reef Rum thats the type of bottle using .
Name is : Tarvey Amber
Size:1l
Alcohol :37.5% Imported Dark Rum
Final designer will be paid extra for posters and t shirt designs. email is dorin@velta-example.co.nz
Target Market(s)
Rum Drinkers .
Industry/Entity Type
Graphic Design
Look and feel
Each slider illustrates characteristics of the customer's brand and the style your logo design should communicate.

```html
<!DOCTYPE html>
<html lang="en">
<head>
<meta charset="utf-8">
<title>Tarvey Amber Dark Rum – Label</title>
<link rel="stylesheet" href="https://fonts.googleapis.com/css2?family=Alfa+Slab+One&family=Kaushan+Script&family=Monsieur+La+Doulaise&family=Roboto+Slab:wght@700&display=swap">
<style>
  :root {
    --canvas: #ffffff;
    --bottle: #3a1d0e;
    --panel: #2b1a0d;
    --gold: #d8b73c;
    --gold-bright: #e3bb45;
    --gold-mid: #c9a23a;
    --gold-deep: #a8822f;
    --brown-dark: #3a2410;
    --imported: #a8957a;
    --white: #ffffff;
    --volume: #6b4a2a;
    --ink: #2b1a0d;
  }
  * { margin: 0; padding: 0; box-sizing: border-box; }
  html, body { width: 1200px; height: 900px; overflow: hidden; background: var(--canvas); }
  .canvas { position: relative; width: 1200px; height: 900px; }

  .bottle { position: absolute; left: 0; top: 0; }

  .label {
    position: absolute;
    background: linear-gradient(135deg, var(--brown-dark) 0%, var(--gold-deep) 22%, var(--gold-mid) 40%, var(--gold-bright) 55%, var(--gold-mid) 72%, var(--brown-dark) 100%);
    text-align: center;
  }
  .label__panel {
    position: absolute;
    background: var(--panel);
    border: 3px solid var(--gold-mid);
    border-radius: 6px;
    box-shadow: inset 0 0 0 3px var(--panel), inset 0 0 0 5px rgba(201,162,58,.45);
  }
  .label__imported {
    position: absolute; left: 0; right: 0;
    font-family: "Alfa Slab One", serif;
    color: var(--imported);
    letter-spacing: .04em;
    opacity: .85;
  }
  .label__brand {
    position: absolute; left: 0; right: 0;
    font-family: "Kaushan Script", cursive;
    color: var(--gold);
    line-height: 1;
  }
  .label__type {
    position: absolute;
    font-family: "Monsieur La Doulaise", cursive;
    color: var(--white);
    white-space: nowrap;
  }
  .label__tagline {
    position: absolute; left: 0; right: 0;
    font-family: "Kaushan Script", cursive;
    color: var(--white);
  }
  .label__volume, .label__abv, .label__distributed, .label__distributor {
    position: absolute; left: 0; right: 0;
    font-family: "Roboto Slab", serif;
    font-weight: 700;
  }
  .label__volume, .label__abv { color: var(--volume); }
  .label__distributed, .label__distributor { color: var(--ink); }

  /* Flat label */
  .label--flat { left: 488px; top: 66px; width: 587px; height: 770px; border-radius: 8px; border: 1px solid #6e5a3a; }
  .label--flat .label__panel { left: 24px; top: 84px; width: 538px; height: 625px; }
  .label--flat .label__imported { top: 18px; font-size: 44px; }
  .label--flat .label__brand { font-size: 112px; }
  .label--flat .brand-1 { top: 160px; left: 20px; }
  .label--flat .brand-2 { top: 285px; left: 20px; }
  .label--flat .label__type { left: 272px; top: 400px; font-size: 48px; }
  .label--flat .label__tagline { font-size: 23px; left: 10px; }
  .label--flat .tag-1 { top: 487px; }
  .label--flat .tag-2 { top: 530px; left: -20px; }
  .label--flat .tag-3 { top: 573px; }
  .label--flat .label__volume { top: 630px; font-size: 18px; }
  .label--flat .label__abv { top: 658px; font-size: 14px; }
  .label--flat .label__distributed { top: 721px; font-size: 15px; }
  .label--flat .label__distributor { top: 741px; font-size: 14px; font-weight: 400; letter-spacing: -.02em; }

  /* Label on bottle */
  .label--bottle { left: 113px; top: 397px; width: 219px; height: 388px; }
  .label--bottle .label__panel { left: 9px; top: 40px; width: 196px; height: 315px; border-width: 2px; }
  .label--bottle .label__imported { top: 8px; font-size: 21px; }
  .label--bottle .label__brand { font-size: 44px; }
  .label--bottle .brand-1 { top: 84px; left: 6px; }
  .label--bottle .brand-2 { top: 136px; left: 6px; }
  .label--bottle .label__type { left: 98px; top: 200px; font-size: 19px; }
  .label--bottle .label__tagline { font-size: 9.5px; left: 2px; }
  .label--bottle .tag-1 { top: 244px; }
  .label--bottle .tag-2 { top: 265px; left: -8px; }
  .label--bottle .tag-3 { top: 285px; }
  .label--bottle .label__volume { top: 316px; font-size: 9px; }
  .label--bottle .label__abv { top: 330px; font-size: 6.5px; }
  .label--bottle .label__distributed { top: 360px; font-size: 7.5px; }
  .label--bottle .label__distributor { top: 370px; font-size: 6.5px; font-weight: 400; }
</style>
</head>
<body>
<main class="canvas">

  <svg class="bottle" width="1200" height="900" viewBox="0 0 1200 900" aria-hidden="true">
    <path fill="var(--bottle)" d="
      M186 66 Q186 60 194 60 L232 60 Q240 60 240 66 L240 120 L236 126 L236 132 L240 138 L238 182
      Q244 250 300 300 Q332 330 332 380 L332 830 Q332 846 316 846 L126 846 Q110 846 110 830
      L110 380 Q110 330 142 300 Q198 250 188 182 L186 138 L190 132 L190 126 L186 120 Z"/>
  </svg>

  <section class="label label--bottle" aria-label="Tarvey Amber label on bottle">
    <div class="label__panel"></div>
    <p class="label__imported">IMPORTED</p>
    <p class="label__brand brand-1">Tarvey</p>
    <p class="label__brand brand-2">Amber</p>
    <p class="label__type">Dark Rum</p>
    <p class="label__tagline tag-1">Robust fruity flavours of molasses infused</p>
    <p class="label__tagline tag-2">with honey and chocolate</p>
    <p class="label__tagline tag-3">and a smooth rounded character</p>
    <p class="label__volume">1 Litre</p>
    <p class="label__abv">37.5% Alcohol by Volume</p>
    <p class="label__distributed">Distributed by</p>
    <p class="label__distributor">????????????????????????????????????????</p>
  </section>

  <section class="label label--flat" aria-label="Tarvey Amber label">
    <div class="label__panel"></div>
    <p class="label__imported">IMPORTED</p>
    <p class="label__brand brand-1">Tarvey</p>
    <p class="label__brand brand-2">Amber</p>
    <p class="label__type">Dark Rum</p>
    <p class="label__tagline tag-1">Robust fruity flavours of molasses infused</p>
    <p class="label__tagline tag-2">with honey and chocolate</p>
    <p class="label__tagline tag-3">and a smooth rounded character</p>
    <p class="label__volume">1 Litre</p>
    <p class="label__abv">37.5% Alcohol by Volume</p>
    <p class="label__distributed">Distributed by</p>
    <p class="label__distributor">????????????????????????????????????????</p>
  </section>

</main>
</body>
</html>
```